Web Design Concept for new social network

We need a fresh, vibrant, clean web design layout for a new social network that we are trying to put together.
The site itself will be stuffed with little jquery/css tricks to enable a better/better looking UI (this is where you come in).
Imagine you were re-imagining Rallyhub.. How would you have designed it? The new site, will have a lot of similar functions to RH, and then a few more.
I will need a great looking sign in page in addition to;
The main page will need to have the following elements;
- Profile header.
Profile picture and tabbed area for various pieces of meta data contact details, preferences etc
- A Post Wall (like the wall on RH, but its crossed with a chirply-esque global search/post). People can respond to not only the original message, but can reply to each individual reply.
Instead of LIKE, there will need to be a positive/negative/neutral style option (feel free to get creative with naming). The background of each post will reflect the average rating (pos/nuetral/neg) of the post itself.. so if 100 people click pos, 50 neutral and 1 negative, the bg will mainly be the positive colour).
The feed will include messages by default from many sources (rallyhub/chirply/work loop) there should be somewhere that these can be switched on and off...
Somewhere to post a message - again by default it will post to all networks, but should be able to switch off.
Images/Videos/Text can all be posted to the wall (if you can think of a better name than wall - please use that!)
- Notifications; rather than having them in a drop down menu like rh, i want them to be in a hidden div (one div for each type) that slides open to reveal the notifications.. The default will be that the divs are closed so if there is a new notification there will be a need for something to appear on the screen that the user can click. We will need 3 notification types.
- Calendar; collapsable
- Options for today/this week/month views etc
- Menu system to navigate to other screens.
This should be able to show available things like groups/pages/events (again feel free to rename).
The screens themselves should appear to be stacked (like stacked tiles).
- Search; there should be a search bar somewhere with various options being available.
- Modal popup. I will be using modal popups across the site so will want a consistant feel (should be able to display photos/videos etc)
I will upload some files over the next few days to support the above, but am really looking for your creativity here.
Sites I really like the style of:
- the NEW yardnook (check it out.. its awesome).
- quince
- chirply
I want a really clean interface, modern.. splashes of colour are fine (but only where it will enhance).
Updates
I have added a file to the uploads that gives an idea of how the notifications should be revealed.. Please do not read too much into any styling... i created the pdf just to show how i expect the notifications to be revealed, and that I expect there to be multiple notification types.
Although I deliberately didnt request adverts to be shown in the brief, i also didnt explicitly state that they shouldnt be! The site will NOT feature adverts so please do not show them on the design. Id much rather that the space be used to improve layout.
Target Market(s)
18 to 40 - again, think rallyhub/chirply/workloop
Industry/Entity Type
Events
Look and feel

```html
<!DOCTYPE html>
<html lang="en">
<head>
<meta charset="utf-8">
<title>HangoutHub.net – Profile Wall</title>
<link href="https://fonts.googleapis.com/css2?family=Questrial&family=Arimo:wght@400;700&display=swap" rel="stylesheet">
<style>
:root{
  --bg:#ebeae8;
  --panel:#f9f9f8;
  --white:#ffffff;
  --ink:#3a3a3a;
  --muted:#6e6e6e;
  --accent:#e8524f;
  --accent-soft:#fb6f6c;
  --dark:#4d4d4d;
  --darker:#2b2b2b;
  --line:#d9d9d9;
  --grey-box:#ececec;
  --blue:#2a8fd6;
}
*{box-sizing:border-box;margin:0;padding:0}
html,body{width:1200px;height:874px;overflow:hidden;background:var(--bg)}
body{font-family:"Arimo",Arial,sans-serif;color:var(--ink);font-size:10px}
.canvas{position:relative;width:1200px;height:874px;overflow:hidden;background:radial-gradient(circle at 60% 40%,#f3f2f0 0,var(--bg) 70%)}
.abs{position:absolute}
a{color:var(--accent);text-decoration:none}

/* top account bar */
.account-bar{left:677px;top:0;width:361px;height:32px;background:var(--dark);border-radius:0 0 4px 4px;display:flex;font-family:"Questrial",sans-serif;font-size:14px;color:#e6e6e6}
.account-bar span{flex:auto;text-align:center;line-height:31px;border-left:1px solid #666}
.account-bar span:first-child{border-left:0}

.brand{font-family:"Arimo",sans-serif;font-weight:700;font-size:21px;color:#6a6a6a;letter-spacing:-.5px}
.brand-top{left:174px;top:41px}
.brand-foot{left:857px;top:790px}

.search{left:375px;top:40px;width:202px;height:31px;background:var(--white);border:1px solid #d4d4d4;font-family:"Questrial",sans-serif;font-size:14px;color:#777;padding:7px 9px}
.search svg{position:absolute;right:10px;top:10px}

.section-nav{left:843px;top:44px;display:flex;gap:16px;font-family:"Questrial",sans-serif;font-size:15px;color:#555;align-items:center}
.section-nav .active{background:var(--accent);color:#fff;padding:5px 11px;border-radius:3px}

/* profile sidebar */
.profile-card{left:177px;top:106px;width:100px;height:235px;background:var(--dark);border:1px solid #333;border-radius:4px;overflow:hidden}
.profile-photo{position:absolute;left:9px;top:9px;width:82px;height:84px;border-radius:6px;background:linear-gradient(135deg,#7a5a3a,#b58760 45%,#3a6d3e)}
.profile-name{position:absolute;left:10px;top:104px;color:#fff;font-weight:700;font-size:11px}
.profile-menu{position:absolute;top:131px;left:0;width:100%}
.profile-menu div{height:20px;line-height:20px;padding-left:11px;color:#e4e4e4;font-weight:700;font-size:10px;border-top:1px solid #5c5c5c}
.profile-menu .on{background:#111;color:#fff;height:21px;border-top:0}

.friends{left:179px;top:349px;display:grid;grid-template-columns:42px 42px;column-gap:11px;row-gap:10px}
.friend{width:42px;height:42px;border:2px solid #fff;box-shadow:0 0 0 1px #ccc;background:linear-gradient(160deg,#c9a48a,#7f6656)}
.friends-count{left:178px;top:507px;width:98px;border-top:1px solid var(--line);padding-top:6px;display:flex;justify-content:space-between;font-size:10px;font-weight:700;color:#555}
.friends-count a{font-weight:400;text-decoration:underline;font-size:9px}

/* info panel */
.info-panel{left:285px;top:105px;width:752px;height:145px;background:var(--panel);border-radius:3px}
.info-tabs{left:943px;top:97px;display:flex;gap:6px}
.info-tabs i{width:21px;height:21px;display:block;border-radius:2px}
.info-rows{position:absolute;left:0;top:19px;width:100%}
.info-row{height:17.6px;border-bottom:1px dotted #ccc;display:flex;align-items:center;font-size:9.5px;position:relative}
.info-row:last-child{border-bottom:0}
.info-row .label{width:103px;padding-left:20px;font-weight:700;font-size:10.5px;color:#333;position:relative}
.info-row .label:before{content:"";position:absolute;left:20px;top:4px;width:5px;height:5px;background:var(--accent);margin-left:-15px}
.info-row .value{color:#444}
.info-row .edit{position:absolute;left:688px;color:#555;font-size:9px;display:flex;gap:6px;align-items:center}
.side-tools{left:1038px;top:123px;display:flex;flex-direction:column;gap:3px}
.side-tools div{width:21px;height:21px;background:#dcdcdc;border-radius:2px;display:flex;align-items:center;justify-content:center}

/* wall */
.wall{left:285px;top:263px;width:750px;height:493px;background:var(--panel);border-radius:3px}
.composer{left:294px;top:271px;width:731px;height:92px;background:var(--grey-box);border-radius:2px}
.composer-input{left:303px;top:281px;width:712px;height:35px;background:#fff;border:1px solid #d5d5d5;padding:11px 11px;font-size:10.5px;color:#555}
.attach{left:303px;top:333px;display:flex;align-items:center;gap:9px;font-size:10.5px;color:#555}
.attach .gap{width:28px}
.privacy{left:927px;top:334px}
.share{left:955px;top:330px;width:60px;height:20px;background:var(--accent);color:#fff;border-radius:3px;font-family:"Questrial",sans-serif;font-size:15px;text-align:center;line-height:20px}

.post-avatar{left:297px;top:380px;width:43px;height:43px;border-radius:5px;background:linear-gradient(150deg,#b07d5c,#4a3426)}
.post-author{left:351px;top:381px;color:var(--accent);font-weight:700;font-size:11px}
.post-image{left:349px;top:399px;width:96px;height:73px;border:3px solid #fff;box-shadow:0 0 0 1px #ddd;background:linear-gradient(180deg,#8fb3c9 0,#6f9a6a 55%,#b8403a 78%,#555 100%)}
.post-body{left:452px;top:399px;font-size:10.5px;line-height:1.5}
.post-body .cap{color:var(--accent)}
.post-body .links{font-size:9px;margin-top:3px}
.post-body .links span{color:#aaa;margin:0 4px}
.post-body .mood{margin-top:15px;font-size:9px}
.post-time{left:349px;top:480px;display:flex;gap:5px;align-items:center;font-size:10.5px;color:#555}
.likes-bar{left:349px;top:506px;width:635px;height:21px;background:var(--accent-soft);font-size:9px;color:#2a2a2a;display:flex;align-items:center;gap:6px;padding-left:6px;border-bottom:2px solid #e45a57}
.likes-bar:before{content:"";position:absolute;left:45px;top:-7px;border:7px solid transparent;border-top:0;border-bottom-color:var(--accent-soft)}
.likes-bar b{color:#fff;font-weight:400}
.more-comments{left:349px;top:532px;width:635px;height:21px;background:var(--grey-box);border-bottom:2px solid #ddd;display:flex;align-items:center;gap:6px;padding-left:5px;font-size:9.5px;font-style:italic;color:var(--accent)}
.reply{left:349px;width:635px;height:35px;background:var(--grey-box);border-bottom:2px solid #ddd;font-size:9px;color:#333}
.reply .ava{position:absolute;left:5px;top:4px;width:29px;height:28px;border-radius:3px;background:linear-gradient(150deg,#e3bfa0,#a7795a)}
.reply .txt{position:absolute;left:41px;top:6px;line-height:15px}
.reply .txt a{color:var(--accent)}
.reply .when{display:flex;gap:4px;align-items:center;color:#555}
.wisdom{left:349px;top:637px;width:635px;height:32px;background:#fff;border:1px solid #ccc;font-family:"Questrial",sans-serif;font-size:14px;color:#444;padding:7px 10px}
.loading{left:349px;top:673px;width:635px;height:66px;background:linear-gradient(#f7f7f7,#e7e7e7);border:1px solid #ccc;border-radius:3px}

.footer-line{left:164px;top:779px;width:874px;border-top:1px dotted #ccc}
.footer-links{left:166px;top:800px;font-size:10.5px;color:var(--accent)}
.footer-links span{color:#888}
</style>
</head>
<body>
<div class="canvas">

  <nav class="abs account-bar"><span>Updates</span><span>My Profile</span><span>Messages</span><span>Settings</span><span>Sign Out</span></nav>
  <div class="abs brand brand-top">HangoutHub.net</div>
  <div class="abs search">Enter Keyword
    <svg width="11" height="11" viewBox="0 0 11 11"><circle cx="4.2" cy="4.2" r="3.2" fill="none" stroke="#555" stroke-width="1.5"/><path d="M6.6 6.6L10 10" stroke="#555" stroke-width="1.8"/></svg>
  </div>
  <nav class="abs section-nav"><span class="active">Groups</span><span>Pages</span><span>Events</span></nav>

  <aside class="abs profile-card">
    <div class="profile-photo" role="img" aria-label="Profile photo of Daniel Brooks"></div>
    <div class="profile-name">Daniel Brooks</div>
    <div class="profile-menu">
      <div class="on">Wall</div><div>Photos</div><div>Videos</div><div>Pages</div><div>Groups</div>
    </div>
  </aside>
  <div class="abs friends">
    <div class="friend" role="img" aria-label="Friend photo"></div>
    <div class="friend" role="img" aria-label="Friend photo"></div>
    <div class="friend" role="img" aria-label="Friend photo"></div>
    <div class="friend" role="img" aria-label="Friend photo"></div>
    <div class="friend" role="img" aria-label="Friend photo"></div>
    <div class="friend" role="img" aria-label="Friend photo"></div>
  </div>
  <div class="abs friends-count">119 Friends <a>View All</a></div>

  <section class="abs info-panel">
    <div class="info-rows">
      <div class="info-row"><span class="label">Name :</span><span class="value">Daniel Brooks</span><span class="edit"><svg width="10" height="10"><path d="M1 9l1-3 5-5 2 2-5 5z" fill="#e6b422"/></svg>Edit</span></div>
      <div class="info-row"><span class="label">Username :</span><span class="value">http://www.hangouthub.net/danielbrooks</span><span class="edit"><svg width="10" height="10"><path d="M1 9l1-3 5-5 2 2-5 5z" fill="#e6b422"/></svg>Edit</span></div>
      <div class="info-row"><span class="label">Email :</span><span class="value">Primary: danielbrooks@mailbox.net</span><span class="edit"><svg width="10" height="10"><path d="M1 9l1-3 5-5 2 2-5 5z" fill="#e6b422"/></svg>Edit</span></div>
      <div class="info-row"><span class="label">Password :</span><span class="value">Updated about 6 months ago.</span><span class="edit"><svg width="10" height="10"><path d="M1 9l1-3 5-5 2 2-5 5z" fill="#e6b422"/></svg>Edit</span></div>
      <div class="info-row"><span class="label">Networks :</span><span class="value">No Networks</span><span class="edit"><svg width="10" height="10"><path d="M1 9l1-3 5-5 2 2-5 5z" fill="#e6b422"/></svg>Edit</span></div>
      <div class="info-row"><span class="label">Language :</span><span class="value">English (US)</span><span class="edit"><svg width="10" height="10"><path d="M1 9l1-3 5-5 2 2-5 5z" fill="#e6b422"/></svg>Edit</span></div>
    </div>
  </section>
  <div class="abs info-tabs"><i style="background:#555"></i><i style="background:var(--blue)"></i><i style="background:var(--accent)"></i></div>
  <div class="abs side-tools">
    <div><svg width="14" height="14"><circle cx="7" cy="5" r="3" fill="#c0503a"/><rect x="2" y="9" width="10" height="5" rx="2" fill="#c0503a"/></svg></div>
    <div><svg width="14" height="14"><circle cx="7" cy="7" r="4.5" fill="none" stroke="#888" stroke-width="2.5" stroke-dasharray="2 1.5"/><circle cx="7" cy="7" r="2" fill="#888"/></svg></div>
    <div><svg width="14" height="14"><circle cx="7" cy="7" r="6" fill="#888"/><rect x="6" y="6" width="2" height="5" fill="#fff"/><circle cx="7" cy="4" r="1" fill="#fff"/></svg></div>
  </div>

  <main class="abs wall"></main>
  <div class="abs composer"></div>
  <div class="abs composer-input">Dazzle the world... or just share something...</div>
  <div class="abs attach">Attach:
    <svg width="15" height="13"><rect x="1" y="2" width="13" height="10" fill="#e0b84a" stroke="#4a7fb4"/></svg>
    <svg width="17" height="14"><rect x="1" y="4" width="15" height="10" fill="#2e4f7c"/><rect x="1" y="1" width="15" height="3" fill="#333"/></svg>
    <svg width="14" height="14"><rect x="2" y="2" width="10" height="11" fill="#fff" stroke="#556"/><path d="M5 5h5M5 8h5" stroke="#556"/></svg>
    <span class="gap"></span>Instant Invite:
    <svg width="14" height="20"><path d="M5 2v10l-3-2v4l5 5h5v-8l-5-1V2z" fill="var(--blue)"/></svg>
  </div>
  <svg class="abs privacy" width="24" height="11"><rect x="1" y="4" width="8" height="6" fill="#555"/><path d="M3 4V2.5a2 2 0 014 0V4" stroke="#555" fill="none"/><path d="M14 3h8l-4 4z" fill="#3a7bc8"/></svg>
  <div class="abs share">Share</div>

  <div class="abs post-avatar" role="img" aria-label="Poster profile photo"></div>
  <div class="abs post-author">User Name Here</div>
  <div class="abs post-image" role="img" aria-label="Group photo of friends outdoors"></div>
  <div class="abs post-body">
    <div class="cap">Image Caption Here</div>
    <div>yeah i got you back :PPPPPP</div>
    <div class="links"><a>Like</a><span>|</span><a>Comment</a></div>
    <div class="mood"><a>Positive</a><span style="color:#aaa;margin:0 6px">|</span><a>Negative</a><span style="color:#aaa;margin:0 6px">|</span><a>Neutral</a></div>
  </div>
  <div class="abs post-time"><svg width="15" height="12"><rect x="1" y="1" width="13" height="10" fill="#e0b84a" stroke="#4a7fb4"/></svg>16 hours ago</div>

  <div class="abs likes-bar"><svg width="13" height="12"><path d="M1 5h3v7H1zM5 5l3-5 2 1-1 4h4v6H5z" fill="#f3d27a"/></svg><span><b>Lena Marsh</b> and <b>Ana Rivers</b> like this</span></div>
  <div class="abs more-comments"><svg width="14" height="12"><rect x="1" y="1" width="12" height="8" rx="2" fill="#fff" stroke="#888"/><path d="M4 9v3l3-3" fill="#fff" stroke="#888"/></svg>Show all 12 comments</div>
  <div class="abs reply" style="top:559px"><div class="ava" role="img" aria-label="Commenter photo"></div><div class="txt"><a>Ana Rivers</a> like this<div class="when"><svg width="13" height="11"><rect x="1" y="1" width="11" height="9" fill="#e0b84a" stroke="#4a7fb4"/></svg>about an hour ago</div></div></div>
  <div class="abs reply" style="top:598px"><div class="ava" role="img" aria-label="Commenter photo"></div><div class="txt"><a>Ana Rivers</a> like this<div class="when"><svg width="13" height="11"><rect x="1" y="1" width="11" height="9" fill="#e0b84a" stroke="#4a7fb4"/></svg>about an hour ago</div></div></div>
  <div class="abs wisdom">Drop some of your wisdom on em</div>
  <div class="abs loading">
    <svg style="position:absolute;left:302px;top:19px" width="28" height="28" viewBox="0 0 28 28">
      <g fill="#444"><circle cx="14" cy="3" r="2.4"/><circle cx="21.8" cy="6.2" r="2.2" opacity=".9"/><circle cx="25" cy="14" r="2" opacity=".8"/><circle cx="21.8" cy="21.8" r="2" opacity=".7"/><circle cx="14" cy="25" r="2" opacity=".6"/><circle cx="6.2" cy="21.8" r="2" opacity=".5"/><circle cx="3" cy="14" r="2" opacity=".4"/><circle cx="6.2" cy="6.2" r="2" opacity=".3"/></g>
    </svg>
  </div>

  <div class="abs footer-line"></div>
  <footer class="abs footer-links">About <span>-</span> Help <span>-</span> Blog <span>-</span> Status <span>-</span> Jobs <span>-</span> Terms <span>-</span> Privacy <span>-</span> Advertisers <span>-</span> Businesses <span>-</span> Media <span>-</span> Developers <span>-</span> Resources <span>-</span> Directory</footer>
  <div class="abs brand brand-foot">HangoutHub.net</div>

</div>
</body>
</html>
```